TK Stationery - Modern Contemporary

Develop modern template for Letterhead and Stationery (business card, letterhead, envelopes) using the TK Logo and Icon

Colors
0054AA
0677BA
7BADD7
CADEEF
E8F1F8
00AB8E
00BBA5
67D7C9
C6EFE9
E9F9F6
EE7325
F08F49
F5BC92
FAE3D3
FDF4ED
6B429C
8869AF
B7A5CE
E3DAEB
F3F0F8

```html
<!DOCTYPE html>
<html lang="en">
<head>
<meta charset="utf-8">
<title>Tessa Kern Letterhead</title>
<link rel="stylesheet" href="https://fonts.googleapis.com/css2?family=Arimo:wght@400&family=Questrial&display=swap">
<style>
  :root {
    --backdrop: #cdcccd;
    --paper: #ffffff;
    --navy: #2a304b;
    --green: #35b172;
    --orange: #ee7325;
    --ink: #555659;
    --footer-text: #ffffff;
  }
  * { box-sizing: border-box; margin: 0; padding: 0; }
  html, body {
    width: 1173px; height: 1200px; overflow: hidden;
    background: var(--backdrop);
  }
  .letterhead {
    position: absolute; left: 230px; top: 95px;
    width: 713px; height: 1009px;
    background: var(--paper);
    box-shadow: 1px 2px 3px rgba(0,0,0,.25);
    overflow: hidden;
  }
  .brand {
    position: absolute; top: 54px; left: 0; width: 100%;
    text-align: center;
    font-family: "Questrial", sans-serif;
    font-size: 36px; line-height: 40px; letter-spacing: 2px;
    color: var(--navy);
  }
  .salutation {
    position: absolute; left: 65px; top: 310px;
    font-family: "Questrial", sans-serif; font-size: 16.5px; font-weight: 700;
    color: var(--ink);
  }
  .letter-body {
    position: absolute; left: 63px; top: 356px; width: 583px;
    font-family: "Arimo", sans-serif; font-size: 12.1px; line-height: 14.8px;
    color: var(--ink); text-align: justify;
  }
  .letter-body p + p { margin-top: 12.5px; }
  .closing {
    position: absolute; left: 65px; top: 755px;
    font-family: "Questrial", sans-serif; font-size: 9.5px; font-weight: 700;
    color: var(--ink);
  }
  .signature {
    position: absolute; left: 64px; top: 798px; width: 117px; height: 35px;
    background: linear-gradient(90deg, #e6e6e7, #d9d9db);
    border-radius: 3px;
  }
  .accent-rule { position: absolute; left: 0; top: 915px; width: 713px; height: 10px; }
  .footer {
    position: absolute; left: 0; top: 925px; width: 713px; height: 84px;
    background: var(--navy); color: var(--footer-text);
    font-family: "Arimo", sans-serif; font-size: 12px; line-height: 14.6px;
  }
  .contact-list { position: absolute; left: 64px; top: 18px; list-style: none; }
  .contact-list li { display: flex; align-items: center; gap: 8px; }
  .contact-list svg { width: 9px; height: 9px; flex: none; }
  .address { position: absolute; right: 64px; top: 18px; text-align: right; font-style: normal; }
</style>
</head>
<body>
  <main class="letterhead">
    <header class="brand">tessa kern</header>

    <h1 class="salutation">Dear Mr. Smith,</h1>

    <section class="letter-body">
      <p>Lorem ipsum dolor sit amet, consectetuer adipiscing elit, sed diam nonmmy nibh euismod tincidunt ut laor eet dolore magna aliquam erat volutpat. Ut wisi enim ad minim veniam, quis nostrud exerci tationmcorper suscipit lobortis nisl ut aliquip ex ea commodo consequat. Duis autem vel eum iriure dolor in hendrerit in vulputate velit esse molestie consequat, vel illum dolore eu feugiat</p>
      <p>Rorem ipsum dolor sit amet, consectetuer adipiscing elit, sed diam nonmmy nibh euismod tincidunt ut laor eet dolore magna aliquam erat volutpat. Ut wisi enim ad minim veniam, quis nostrud exerci tationmcorper suscipit lobortis nisl ut aliquip ex ea commodo consequat. Duis autem vel eum iriure dolor in hendrerit in vulputate velit esse molest</p>
      <p>Dorem ipsum dolor sit amet, consectetuer adipiscing elit, sed diam nonmmy nibh euismod tincidunt ut laor eet dolore magna aliquam erat volutpat. Ut wisi enim ad minim veniam, quis nostrud exerci tationmcorper suscipit lobortis nisl ut aliquip ex ea commodo consequat. Duis autem vel eum iriure dolor in hendrerit in suscipit lobortis nisl ut aliquip ex ea commodo consequat. Duis autem vel eum iriure dolor in hendrerit in vulputate velit esse molestie consequat, vel illum</p>
      <p>Sorem ipsum dolor sit amet, consectetuer adipiscing elit, sed diam nonmmy nibh euismod tincidunt ut laor eet dolore magna aliquam erat volutpat. Ut wisi enim ad minim veniam, quis nostrud exerci tationmcorper suscipit lobortis nisl ut aliquip ex ea commodo consequat. Duis autem vel eum iriure dolor in</p>
    </section>

    <p class="closing">Sincerely,</p>
    <div class="signature" role="img" aria-label="Handwritten signature of the sender"></div>

    <svg class="accent-rule" viewBox="0 0 713 10" aria-hidden="true">
      <rect x="0" y="2.5" width="348" height="4.5" fill="var(--green)"/>
      <rect x="366" y="2.5" width="347" height="4.5" fill="var(--green)"/>
      <circle cx="357" cy="5" r="5" fill="var(--orange)"/>
    </svg>

    <footer class="footer">
      <ul class="contact-list">
        <li>
          <svg viewBox="0 0 10 10" aria-hidden="true"><path d="M2 1.2l1.6-.2.8 2-1 .8a5 5 0 0 0 2.8 2.8l.8-1 2 .8-.2 1.6C6.5 9 1 3.5 2 1.2z" fill="var(--green)"/></svg>
          <span>123-456-2100</span>
        </li>
        <li>
          <svg viewBox="0 0 10 10" aria-hidden="true"><rect x="0.5" y="2" width="9" height="6" fill="var(--green)"/><path d="M0.8 2.3L5 5.6l4.2-3.3" stroke="var(--navy)" stroke-width="0.8" fill="none"/></svg>
          <span>info@tessakern.com</span>
        </li>
        <li>
          <svg viewBox="0 0 10 10" aria-hidden="true"><circle cx="5" cy="5" r="4.3" fill="var(--green)"/><path d="M1 5h8M5 .8c-2 2.5-2 5.9 0 8.4M5 .8c2 2.5 2 5.9 0 8.4" stroke="var(--navy)" stroke-width="0.7" fill="none"/></svg>
          <span>www.tessakern.com</span>
        </li>
      </ul>
      <address class="address">
        Your address<br>
        city<br>
        state, ZIP 0000
      </address>
    </footer>
  </main>
</body>
</html>
```